Upscale business cards needed for Board of Directors

We need professional business cards created for members of our family business Board of Directors. We would like these relatively simple and straightforward, but also with a unique element to set them apart. Probably stick with neutral and simple colors - white, grey etc. We need space for the traditional elements, including name, title, address, email/phone number. And we will be creating several from this template so it needs to be template that is easy to switch information in and out of.
Business
See description

```html
<!DOCTYPE html>
<html lang="en">
<head>
<meta charset="utf-8">
<title>Harborline Holdings – Business Card</title>
<link rel="stylesheet" href="https://fonts.googleapis.com/css2?family=Open+Sans:wght@400;700&display=swap">
<style>
  :root {
    --bg: #e6e6e4;
    --card-dark: #2e2c2d;
    --card-light: #ffffff;
    --ink: #1f1d1e;
    --gold: #b09a6c;
    --muted: #8a8a8a;
    --url-on-dark: #9a9898;
  }
  * { box-sizing: border-box; margin: 0; padding: 0; }
  html, body { width: 1200px; height: 1000px; overflow: hidden; }
  body {
    position: relative;
    background: var(--bg);
    font-family: "Open Sans", Arial, sans-serif;
  }
  .card {
    position: absolute;
    left: 287px;
    width: 626px;
    height: 358px;
    overflow: hidden;
    box-shadow: 0 4px 14px rgba(0,0,0,.18);
  }
  .card--front { top: 140px; background: var(--card-dark); }
  .card--back { top: 531px; background: var(--card-light); }

  .company-name {
    font-weight: 700;
    line-height: 1.2;
    white-space: nowrap;
  }
  .card--front .company-name {
    position: absolute;
    left: 0; right: 0; top: 150px;
    text-align: center;
    color: #ffffff;
    font-size: 40px;
  }
  .card--front .site {
    position: absolute;
    left: 0; right: 0; top: 308px;
    text-align: center;
    color: var(--url-on-dark);
    font-size: 13px;
  }

  .card--back .company-name {
    position: absolute;
    right: 35px; top: 50px;
    text-align: right;
    color: var(--ink);
    font-size: 24px;
  }
  .holder { position: absolute; left: 35px; top: 52px; }
  .holder__name { color: var(--gold); font-weight: 700; font-size: 18px; line-height: 1.1; }
  .holder__title { color: var(--muted); font-size: 13px; margin-top: 2px; }
  .holder-marker { position: absolute; left: 0; top: 56px; }

  .contacts { position: absolute; left: 35px; top: 251px; list-style: none; }
  .contacts li {
    display: flex; align-items: center; gap: 6px;
    color: var(--muted); font-size: 13px; line-height: 18px;
  }
  .contacts svg { width: 11px; height: 11px; flex: none; }

  .address {
    position: absolute; right: 35px; top: 251px;
    text-align: right; color: var(--muted); font-size: 13.5px; line-height: 18px;
    font-style: normal;
  }
  .address__label { color: var(--gold); font-weight: 700; }

  .footer-bands { position: absolute; left: 0; bottom: 0; }
</style>
</head>
<body>
  <section class="card card--front">
    <p class="company-name">Harborline Holdings</p>
    <p class="site">www.harborlineholdings.com</p>
  </section>

  <section class="card card--back">
    <svg class="holder-marker" width="24" height="32" viewBox="0 0 24 32" aria-hidden="true">
      <polygon points="0,0 10,0 6,32 0,32" fill="var(--ink)"/>
      <polygon points="13,0 24,0 24,32 9,32" fill="var(--gold)"/>
    </svg>
    <div class="holder">
      <p class="holder__name">Daniel Reed</p>
      <p class="holder__title">President</p>
    </div>

    <p class="company-name">Harborline Holdings</p>

    <ul class="contacts">
      <li>
        <svg viewBox="0 0 11 11" aria-hidden="true"><rect x="2.5" y="0.5" width="6" height="10" rx="1" fill="none" stroke="var(--muted)"/><circle cx="5.5" cy="8.8" r="0.7" fill="var(--muted)"/></svg>
        012-555-0147
      </li>
      <li>
        <svg viewBox="0 0 11 11" aria-hidden="true"><rect x="0.5" y="2" width="10" height="7" fill="var(--muted)"/><polyline points="0.5,2 5.5,6 10.5,2" fill="none" stroke="#fff" stroke-width="0.9"/></svg>
        info@harborlineholdings.com
      </li>
      <li>
        <svg viewBox="0 0 11 11" aria-hidden="true"><circle cx="5.5" cy="5.5" r="4.8" fill="none" stroke="var(--muted)"/><ellipse cx="5.5" cy="5.5" rx="2" ry="4.8" fill="none" stroke="var(--muted)" stroke-width="0.8"/><line x1="0.7" y1="5.5" x2="10.3" y2="5.5" stroke="var(--muted)" stroke-width="0.8"/></svg>
        www.harborlineholdings.com
      </li>
    </ul>

    <address class="address">
      <span class="address__label">Address</span><br>
      Street name, Suite 100 State,<br>
      Zip Code, Country
    </address>

    <svg class="footer-bands" width="626" height="24" viewBox="0 0 626 24" aria-hidden="true">
      <rect x="0" y="11" width="306" height="13" fill="var(--ink)"/>
      <polygon points="316,0 626,0 626,24 291,24" fill="var(--gold)"/>
    </svg>
  </section>
</body>
</html>
```